Corvane Holdings , new business card design

investment firm with corporate clients . need double sided business card , vertical and horizontal options ,logo must be clear. prefer pantone colors only and sharp design. website also www.corvane.ae

Khalid Bin Tarrafi
Managing Director
Tel. +971 4 387 2940
Mobile +971 50 518 2403
khalid@corvane.ae
Q-Span Plaza, officw 18-B07, Warqa Gardens, Dubai

Contact Information for Business Card

Khalid Bin Tarrafi
Managing Director

Font styles to use
Serif

Colors

Designer to choose colors to be used in the design.

```html
<!DOCTYPE html>
<html lang="en">
<head>
<meta charset="utf-8">
<title>Corvane Holdings — Business Card</title>
<link rel="stylesheet" href="https://fonts.googleapis.com/css2?family=Mulish:wght@300;400;800&display=swap">
<style>
  :root {
    --backdrop: #e8e5e2;
    --card: #ffffff;
    --navy: #0f2763;
    --steel: #4f78a3;
    --slate: #6f6f80;
    --ink: #2b2b33;
    --muted: #5a5a66;
  }
  * { margin: 0; padding: 0; box-sizing: border-box; }
  html, body {
    width: 1200px; height: 997px; overflow: hidden;
    background: var(--backdrop);
    font-family: "Mulish", Arial, sans-serif;
  }
  .canvas { position: relative; width: 1200px; height: 997px; }
  .card {
    position: absolute; width: 620px; height: 354px;
    background: var(--card);
    box-shadow: 0 6px 18px rgba(0,0,0,0.12);
    overflow: hidden;
  }
  .card--front { left: 290px; top: 114px; }
  .card--back { left: 290px; top: 528px; }

  .wordmark { display: flex; align-items: center; gap: 12px; }
  .wordmark__square { width: 14px; height: 14px; background: var(--steel); }
  .wordmark__name {
    font-weight: 300; color: var(--ink);
    letter-spacing: 0.28em; text-transform: uppercase; white-space: nowrap;
  }
  .card--front .wordmark { position: absolute; left: 40px; top: 92px; }
  .card--front .wordmark__name { font-size: 18px; }
  .card--back .wordmark { position: absolute; left: 50%; top: 50%; transform: translate(-50%, -50%); }
  .card--back .wordmark__name { font-size: 24px; }

  .identity { position: absolute; left: 108px; top: 205px; }
  .identity__name { font-weight: 800; font-size: 16px; color: var(--navy); letter-spacing: 0.02em; text-transform: uppercase; }
  .identity__title { font-weight: 400; font-size: 14px; color: var(--muted); margin-top: 2px; }

  .wave { position: absolute; inset: 0; width: 620px; height: 354px; }

  .contact {
    position: absolute; right: 24px; top: 138px;
    color: #ffffff; text-align: right;
    font-size: 12.5px; line-height: 1.55; font-weight: 400;
  }
  .contact__row { display: flex; justify-content: flex-end; align-items: center; gap: 6px; }
  .contact__icon { width: 11px; height: 11px; flex: none; }
</style>
</head>
<body>
<div class="canvas">

  <section class="card card--front" aria-label="Card front">
    <svg class="wave" viewBox="0 0 620 354" aria-hidden="true">
      <path d="M620 70 C530 70, 455 75, 410 112 C355 160, 320 320, 175 354 L190 354 C330 326, 368 168, 420 121 C462 86, 535 80, 620 80 Z" fill="var(--slate)"/>
      <path d="M620 90 C540 90, 470 95, 430 130 C380 175, 340 330, 200 354 L620 354 Z" fill="var(--navy)"/>
      <path d="M620 97 C545 97, 478 102, 440 136 C392 180, 352 332, 215 354" fill="none" stroke="#ffffff" stroke-width="2"/>
    </svg>

    <div class="wordmark">
      <span class="wordmark__square"></span>
      <span class="wordmark__name">Corvane Holdings</span>
    </div>

    <div class="identity">
      <p class="identity__name">Khalid Bin Tarrafi</p>
      <p class="identity__title">Managing Director</p>
    </div>

    <div class="contact">
      <p class="contact__row">+971 4 387 2940
        <svg class="contact__icon" viewBox="0 0 12 12"><path d="M3 1 L5 3.5 L4 5 C5 7 6 8 7.5 8.5 L9 7.5 L11 9.5 L9.5 11 C5 10.5 1.5 7 1 2.5 Z" fill="#fff"/></svg>
      </p>
      <p class="contact__row">+971 50 518 2403
        <svg class="contact__icon" viewBox="0 0 12 12"><rect x="3" y="0.5" width="6" height="11" rx="1.2" fill="#fff"/><rect x="4" y="2" width="4" height="6" fill="var(--navy)"/><circle cx="6" cy="9.7" r="0.8" fill="var(--navy)"/></svg>
      </p>
      <p class="contact__row">khalid@corvane.ae
        <svg class="contact__icon" viewBox="0 0 12 12"><rect x="0.5" y="2.5" width="11" height="7" fill="none" stroke="#fff" stroke-width="1.2"/><path d="M0.5 2.5 L6 7 L11.5 2.5" fill="none" stroke="#fff" stroke-width="1.2"/></svg>
      </p>
      <p>Q-Span Plaza, officw 18-B07,</p>
      <p>Warqa Gardens, Dubai</p>
    </div>
  </section>

  <section class="card card--back" aria-label="Card back">
    <div class="wordmark">
      <span class="wordmark__square"></span>
      <span class="wordmark__name">Corvane Holdings</span>
    </div>
  </section>

</div>
</body>
</html>
```